U.S. Popcorn company needs business cards

We are a popcorn company that manufactures popcorn and sells it to grocery stores worldwide. Our theme is "Americana" and our logo is U.S. route 66 which is the most famous highway in the U.S.

We would like the design to be simple and to use both sides. On the back side we would like to see just the logo and website. The front would be normal details

Target Market(s)

Wholesalers, grocers and distributors

Industry/Entity Type

Manufacture

Contact Information for Business Card

Business name: Prairie Lantern Popcorn
Phone: +1 555 308 4726
Email: Dale@prairielanternpopcorn.com
website: www.prairielanternpopcorn.com
Tag Line: "POPular for a reason"
Name: Dale Whitcombe
Title: Founder/President

Requirements
Must have
• Either this design should be fun or clean and simple. I will let you show me your thougths.
Nice to have
• Anything that ties in the real Hwy Route 66.
• Colors might need to be red, white and blue incorporated.
Should not have
• Not be too busy.

```html
<!DOCTYPE html>
<html lang="en">
<head>
<meta charset="utf-8">
<title>Prairie Lantern Popcorn – Business Cards</title>
<link rel="stylesheet" href="https://fonts.googleapis.com/css2?family=Lato:wght@400;700&family=Raleway:wght@700&family=Delius&display=swap">
<style>
  :root {
    --navy: #14296b;
    --red: #e31e24;
    --ink: #1c1c1c;
    --card: #ffffff;
    --backdrop: #f2f2f2;
    --divider: #3a3a3a;
  }
  * { box-sizing: border-box; margin: 0; padding: 0; }
  html, body { width: 1200px; height: 586px; overflow: hidden; }
  body { background: var(--backdrop); position: relative; font-family: "Lato", sans-serif; color: var(--ink); }

  .card {
    position: absolute;
    top: 128px;
    width: 502px;
    height: 302px;
    background: var(--card);
    overflow: hidden;
  }
  .card--back { left: 61px; }
  .card--front { left: 619px; }

  .brand-band {
    position: absolute;
    left: 0; bottom: 0;
    width: 502px; height: 16px;
    display: block;
  }

  .brand-name {
    display: flex;
    align-items: center;
    gap: 10px;
    font-family: "Raleway", sans-serif;
    font-weight: 700;
    color: var(--navy);
    text-align: center;
  }
  .brand-name__dot {
    flex: none;
    border-radius: 50%;
    background: var(--red);
  }

  /* back side */
  .card--back .brand-name {
    position: absolute;
    left: 0; right: 0; top: 90px;
    justify-content: center;
    font-size: 26px;
    line-height: 1.15;
  }
  .card--back .brand-name__dot { width: 18px; height: 18px; }
  .tagline {
    position: absolute;
    left: 0; right: 0; top: 254px;
    text-align: center;
    font-family: "Delius", cursive;
    font-size: 12px;
    letter-spacing: 2.4px;
    color: var(--ink);
  }

  /* front side */
  .card--front .brand-name {
    position: absolute;
    left: 18px; top: 108px;
    width: 190px;
    justify-content: center;
    font-size: 19px;
    line-height: 1.2;
  }
  .card--front .brand-name__dot { width: 14px; height: 14px; }
  .divider {
    position: absolute;
    left: 230px; top: 58px;
    width: 2px; height: 196px;
    background: linear-gradient(to bottom, transparent, var(--divider) 30%, var(--divider) 70%, transparent);
  }
  .person {
    position: absolute;
    left: 251px; top: 84px;
  }
  .person__name {
    font-family: "Raleway", sans-serif;
    font-weight: 700;
    font-size: 17px;
    color: var(--red);
  }
  .person__title {
    font-size: 11.5px;
    margin-top: 3px;
  }
  .contact-list {
    position: absolute;
    left: 251px; top: 160px;
    list-style: none;
  }
  .contact-list li {
    display: flex;
    align-items: center;
    gap: 9px;
    height: 24.5px;
    font-weight: 700;
    font-size: 12px;
  }
  .contact-list svg { width: 12px; height: 12px; flex: none; }
</style>
</head>
<body>

<section class="card card--back" aria-label="Card back">
  <div class="brand-name"><span class="brand-name__dot"></span>Prairie Lantern<br>Popcorn</div>
  <p class="tagline">POPular for a reason</p>
  <svg class="brand-band" viewBox="0 0 502 16" aria-hidden="true">
    <path d="M0 4 H312 Q302 8 298 16 H0 Z" fill="var(--navy)"/>
    <path d="M306 16 Q312 0 336 0 H502 V16 Z" fill="var(--red)"/>
  </svg>
</section>

<section class="card card--front" aria-label="Card front">
  <div class="brand-name"><span class="brand-name__dot"></span>Prairie Lantern<br>Popcorn</div>
  <div class="divider"></div>
  <div class="person">
    <p class="person__name">Dale Whitcombe</p>
    <p class="person__title">Founder/President</p>
  </div>
  <ul class="contact-list">
    <li>
      <svg viewBox="0 0 24 24" aria-hidden="true"><path fill="var(--navy)" d="M2 8c0-3 4-5 10-5s10 2 10 5v2h-5V8c-2-1-8-1-10 0v2H2zM7 11h10l3 9H4z"/></svg>
      +1 555 308 4726
    </li>
    <li>
      <svg viewBox="0 0 24 24" aria-hidden="true"><rect x="1" y="4" width="22" height="16" fill="var(--navy)"/><path d="M2 5l10 8 10-8" stroke="#fff" stroke-width="1.8" fill="none"/></svg>
      Dale@prairielanternpopcorn.com
    </li>
    <li>
      <svg viewBox="0 0 24 24" aria-hidden="true"><g fill="none" stroke="var(--navy)" stroke-width="3" stroke-linecap="round"><path d="M10 14a5 5 0 0 0 7 0l3-3a5 5 0 0 0-7-7l-1 1"/><path d="M14 10a5 5 0 0 0-7 0l-3 3a5 5 0 0 0 7 7l1-1"/></g></svg>
      www.prairielanternpopcorn.com
    </li>
  </ul>
  <svg class="brand-band" viewBox="0 0 502 16" aria-hidden="true">
    <path d="M0 4 H312 Q302 8 298 16 H0 Z" fill="var(--navy)"/>
    <path d="M306 16 Q312 0 336 0 H502 V16 Z" fill="var(--red)"/>
  </svg>
</section>

</body>
</html>
```